Party Favors and Decorations Business Needs A Business Card Design

We are in need of a Logo design and business card design for a new small business called Bright Lantern Designs. We create party decorations and favours for Bridal Showers, Baby Showers, Weddings Birthdays etc. This is a very personalized service based on Clients theme, colour, and style. We are looking for a high end elegant look. I have attached a file to the style I like including the type of paper.

Target Market(s)

women, young adults, expectant mothers, mothers

Industry/Entity Type

Small Business

Contact Information for Business Card

Bright Lantern Designs Essex, ON 519-847-2061 brightlanterndesigns.ca karen@brightlanterngiftbox.com find us on Chatterly

Logo Text

Bright Lantern Designs

Font styles to use
Script

Requirements
Must have
• Name, email, web address, phone number
Should not have
• cutesy graphics

```html
<!DOCTYPE html>
<html lang="en">
<head>
<meta charset="utf-8">
<title>Bright Lantern Designs – Business Card</title>
<link rel="stylesheet" href="https://fonts.googleapis.com/css2?family=Arimo:wght@400;700&family=Courgette&family=Playfair+Display:wght@700&display=swap">
<style>
  :root {
    --page: #e9e7e3;
    --ink: #111111;
    --paper: #ffffff;
    --rule: #bdbdbd;
  }
  * { box-sizing: border-box; margin: 0; padding: 0; }
  html, body { width: 1200px; height: 892px; overflow: hidden; }
  body { background: var(--page); position: relative; font-family: "Arimo", sans-serif; }

  .card {
    position: absolute;
    left: 250px;
    width: 700px;
    height: 400px;
    background: var(--paper);
    overflow: hidden;
    box-shadow: 0 6px 18px rgba(0,0,0,0.18);
  }
  .card-front { top: 31px; }
  .card-back { top: 461px; }
  .card-shape { position: absolute; inset: 0; width: 700px; height: 400px; }

  .wordmark {
    font-family: "Playfair Display", serif;
    font-weight: 700;
    line-height: 1.05;
    position: absolute;
  }
  .card-front .wordmark {
    left: 70px; top: 34px;
    font-size: 40px;
    color: var(--paper);
  }
  .card-back .wordmark {
    left: 0; right: 0; top: 140px;
    text-align: center;
    font-size: 54px;
    color: var(--ink);
  }

  .person { position: absolute; left: 90px; top: 205px; color: var(--paper); }
  .person-name { font-family: "Courgette", cursive; font-size: 30px; }
  .person-role { font-size: 15px; margin-top: 2px; padding-left: 26px; }

  .divider {
    position: absolute; left: 345px; top: 200px;
    width: 1px; height: 150px; background: var(--rule);
  }

  .contacts { position: absolute; left: 368px; top: 210px; list-style: none; color: var(--paper); }
  .contacts li { display: flex; align-items: center; gap: 10px; font-size: 17px; height: 27px; }
  .contacts svg { width: 14px; height: 14px; flex: none; }
  .social { margin-top: 4px; }
  .social-box { width: 22px; height: 22px; background: var(--paper); flex: none; }
  .social-text { font-size: 10px; line-height: 1.1; }
  .social-text strong { display: block; font-size: 15px; font-weight: 700; }
</style>
</head>
<body>
  <section class="card card-front" aria-label="Business card front">
    <svg class="card-shape" viewBox="0 0 700 400" aria-hidden="true">
      <polygon points="0,0 560,0 700,170 700,400 150,400 0,140" fill="var(--ink)"/>
    </svg>
    <p class="wordmark">Bright Lantern<br>Designs</p>
    <div class="person">
      <p class="person-name">Employee name</p>
      <p class="person-role">Managing Director</p>
    </div>
    <div class="divider"></div>
    <ul class="contacts">
      <li>
        <svg viewBox="0 0 24 24"><path fill="var(--paper)" d="M6.6 10.8a15 15 0 0 0 6.6 6.6l2.2-2.2c.3-.3.7-.4 1-.2 1.1.4 2.3.6 3.6.6.6 0 1 .4 1 1V20c0 .6-.4 1-1 1A17 17 0 0 1 3 4c0-.6.4-1 1-1h3.5c.6 0 1 .4 1 1 0 1.2.2 2.4.6 3.6.1.3 0 .7-.2 1z"/></svg>
        <span>519-847-2061</span>
      </li>
      <li>
        <svg viewBox="0 0 24 24"><circle cx="12" cy="12" r="9" fill="none" stroke="var(--paper)" stroke-width="2.5"/><path d="M3 12h18M12 3c3 3 3 15 0 18M12 3c-3 3-3 15 0 18" fill="none" stroke="var(--paper)" stroke-width="1.8"/></svg>
        <span>www.brightlanterndesigns.ca</span>
      </li>
      <li>
        <svg viewBox="0 0 24 24"><rect x="2" y="5" width="20" height="14" fill="var(--paper)"/><path d="M2 5l10 8 10-8" fill="none" stroke="var(--ink)" stroke-width="2"/></svg>
        <span>karen@brightlanterngiftbox.com</span>
      </li>
      <li class="social">
        <span class="social-box"></span>
        <span class="social-text">Find us on<strong>Chatterly</strong></span>
      </li>
    </ul>
  </section>

  <section class="card card-back" aria-label="Business card back">
    <svg class="card-shape" viewBox="0 0 700 400" aria-hidden="true">
      <polygon points="0,0 200,0 0,110" fill="var(--ink)"/>
      <polygon points="700,220 700,400 420,400" fill="var(--ink)"/>
    </svg>
    <p class="wordmark">Bright Lantern<br>Designs</p>
  </section>
</body>
</html>
```